Art Business Needs a Wordpress Theme

I need a Wordpress theme for my company, Pim Pim Nook. Pim Pim stands for Love, Local and the company's focus is to increase awareness of local art and artists. The site will have a blog with posts that showcase local art, art how-to techniques, featured artists and art events. These could be broken down into separate pages or just kept within the homepage. I have a logo that I would like to incorporate. The only request I will make about the layout is that it can feature pictures prominently. Eventually with the help of a Fundmoor campaign I would like to turn the site into an upscale e-commerce platform for member artists of the site. The blog that you are designing will be built on as the business grows into its full vision.

Target Market(s)

Young professionals, Art fans and home designers

Industry/Entity Type

Business

Number of Pages Required

3 page

Font styles to use
Sans Serif

Colors
eda3c7
e667a6
e34197
f59195
f04a50
f68d4d
f37122

Requirements
Must have
• An about page and a contact page. I would like it if the logo was featured on the top left of the screen along with the words Love. Local. Art.
Nice to have
• Perhaps if possible it would be cool to have a way for people to enter their email if they were interested in joining a mailing list or having the Social media information displayed on a sidebar.

```html
<!DOCTYPE html>
<html lang="en">
<head>
<meta charset="utf-8">
<title>Pim Pim Nook</title>
<link href="https://fonts.googleapis.com/css2?family=Roboto:wght@400;500;700&family=Quicksand:wght@600&display=swap" rel="stylesheet">
<style>
  :root{
    --pink-light:#eda3c7;
    --pink:#e667a6;
    --magenta:#e34197;
    --magenta-deep:#b81f6f;
    --salmon:#f59195;
    --red:#f04a50;
    --peach:#f68d4d;
    --orange:#f37122;
    --bg-light:#ecb3d0;
    --bg-deep:#c25d97;
    --panel:rgba(250,200,222,.72);
    --text-dark:#5a3448;
    --white:#ffffff;
  }
  *{box-sizing:border-box;margin:0;padding:0}
  html,body{width:843px;height:1200px;overflow:hidden}
  body{
    position:relative;
    font-family:"Roboto",Arial,sans-serif;
    color:var(--text-dark);
    background:
      radial-gradient(ellipse 360px 300px at 130px 170px,var(--bg-light) 0%,rgba(236,179,208,0) 100%),
      radial-gradient(ellipse at 40% 35%,#d98ab7 0%,var(--bg-deep) 70%,#b24f88 100%);
  }
  a{text-decoration:none}
  .site-header{position:absolute;left:0;top:0;width:843px;height:330px}
  .header-photo{
    position:absolute;left:282px;top:0;width:518px;height:304px;
    border:7px solid var(--white);border-top:0;
    background:linear-gradient(135deg,#e9d7c8 0%,#c9a98e 45%,#8d6b57 75%,#d7c1b0 100%);
    box-shadow:0 3px 8px rgba(0,0,0,.25);
  }
  .brand{position:absolute;left:26px;top:178px;display:flex;align-items:center;gap:10px}
  .brand-mark{width:28px;height:28px;border-radius:50%;background:var(--magenta)}
  .brand-name{font-family:"Quicksand","Roboto",sans-serif;font-weight:600;font-size:25px;color:var(--magenta-deep);white-space:nowrap}

  .main-nav{
    position:absolute;left:56px;top:343px;width:731px;height:38px;
    background:var(--red);display:flex;align-items:center;padding:0 14px;
    box-shadow:0 2px 0 #c83238;
  }
  .main-nav a{color:var(--white);font-size:10px;font-weight:500;margin-right:32px;letter-spacing:.3px}
  .nav-search{margin-left:auto;width:152px;height:20px;background:var(--white);display:flex;align-items:center;justify-content:space-between;padding:0 6px;font-size:9px;color:#999}
  .nav-search svg{width:11px;height:11px}

  .section-title{position:absolute;left:56px;top:418px;font-size:17px;font-weight:700;color:var(--white);letter-spacing:.5px}

  .post{position:absolute;left:56px;width:548px;height:190px;background:var(--panel);padding:10px}
  .post-date{position:absolute;left:0;top:10px;width:56px;height:36px;background:var(--magenta);color:var(--white);display:flex;align-items:center;justify-content:center;gap:4px}
  .post-date .month{font-size:8px;line-height:1;text-align:right}
  .post-date .day{font-size:22px;font-weight:700}
  .post-title{position:absolute;left:66px;top:10px;font-size:16px;font-weight:700;color:var(--magenta);white-space:nowrap}
  .post-meta{position:absolute;left:66px;top:32px;font-size:8px;color:#8a5570}
  .post-meta b{color:var(--orange);font-weight:500}
  .post-photo{position:absolute;left:10px;top:54px;width:186px;height:124px}
  .photo-a{background:linear-gradient(135deg,#7a9a70,#c6b39a,#5e6f88)}
  .photo-b{background:linear-gradient(135deg,#3e6fa8,#c37a8f,#e0c36c)}
  .photo-c{background:linear-gradient(135deg,#c85a3c,#6aa0c0,#d7b34a)}
  .post-excerpt{position:absolute;left:210px;top:58px;width:320px;font-size:9px;line-height:1.55;color:var(--text-dark)}
  .btn{display:inline-block;background:var(--orange);color:var(--white);font-size:8px;font-weight:500;padding:6px 12px;letter-spacing:.3px}
  .post .btn{position:absolute;left:210px;top:150px}

  .pagination{position:absolute;left:258px;top:1098px;display:flex;gap:4px}
  .pagination span{width:16px;height:16px;background:var(--white);font-size:8px;display:flex;align-items:center;justify-content:center;color:var(--text-dark)}
  .pagination .current,.pagination .arrow{background:var(--orange);color:var(--white)}

  .widget{position:absolute;left:624px;width:163px;background:var(--panel);padding:10px}
  .widget-title{font-size:14px;font-weight:700;color:var(--white);padding-bottom:6px;border-bottom:1px solid rgba(255,255,255,.7);margin-bottom:8px;line-height:1.15}
  .widget p{font-size:8px;line-height:1.5}
  .widget .btn{float:right;margin-top:8px}
  .social{display:flex;gap:6px}
  .social span{width:20px;height:20px;border-radius:50%}
  .social .s1{background:#3b5b98}.social .s2{background:#3a9a6a}.social .s3{background:#d24a3c}.social .s4{background:#c9373f}
  .email-field{width:100%;height:20px;background:var(--white);font-size:8px;color:#999;padding:0 6px;display:flex;align-items:center}

  .site-footer{position:absolute;left:0;top:1124px;width:843px;height:76px;background:var(--orange);display:flex;align-items:center;justify-content:center;font-size:8px;color:var(--white)}
</style>
</head>
<body>
  <header class="site-header">
    <div class="header-photo" role="img" aria-label="Photo of a local artist painting at a low wooden table in a studio"></div>
    <div class="brand"><span class="brand-mark"></span><span class="brand-name">Pim Pim Nook</span></div>
  </header>

  <nav class="main-nav">
    <a href="#">HOME</a><a href="#">ABOUT</a><a href="#">BLOG</a><a href="#">FEATURED ARTISTS</a><a href="#">FEATURED ARTISTS</a><a href="#">CONTACT</a>
    <div class="nav-search">Search
      <svg viewBox="0 0 12 12"><circle cx="5" cy="5" r="3.5" fill="none" stroke="#f04a50" stroke-width="1.6"/><line x1="7.6" y1="7.6" x2="11" y2="11" stroke="#f04a50" stroke-width="1.8"/></svg>
    </div>
  </nav>

  <h2 class="section-title">BLOG POSTS</h2>

  <article class="post" style="top:452px">
    <div class="post-date"><span class="month">JUL<br>2015</span><span class="day">15</span></div>
    <h3 class="post-title">Vestibulum ante ipsum primis in faucibus orci luctus...</h3>
    <p class="post-meta">Posted by <b>Admin</b> in <b>Local Art</b></p>
    <div class="post-photo photo-a" role="img" aria-label="Photo of a street art market with artists at work"></div>
    <p class="post-excerpt">Local painters open their studios this month to share new work, quiet methods and stories behind each piece. Visit the gallery walk and meet the makers in person.</p>
    <a class="btn" href="#">READ MORE</a>
  </article>

  <article class="post" style="top:670px">
    <div class="post-date"><span class="month">JUL<br>2015</span><span class="day">15</span></div>
    <h3 class="post-title">Vestibulum ante ipsum primis in faucibus orci luctus...</h3>
    <p class="post-meta">Posted by <b>Admin</b> in <b>Local Art</b></p>
    <div class="post-photo photo-b" role="img" aria-label="Photo of colourful painted artworks on display"></div>
    <p class="post-excerpt">Local painters open their studios this month to share new work, quiet methods and stories behind each piece. Visit the gallery walk and meet the makers in person.</p>
    <a class="btn" href="#">READ MORE</a>
  </article>

  <article class="post" style="top:888px">
    <div class="post-date"><span class="month">JUL<br>2015</span><span class="day">15</span></div>
    <h3 class="post-title">Vestibulum ante ipsum primis in faucibus orci luctus...</h3>
    <p class="post-meta">Posted by <b>Admin</b> in <b>Local Art</b></p>
    <div class="post-photo photo-c" role="img" aria-label="Photo of handmade crafts and textiles at a local market"></div>
    <p class="post-excerpt">Local painters open their studios this month to share new work, quiet methods and stories behind each piece. Visit the gallery walk and meet the makers in person.</p>
    <a class="btn" href="#">READ MORE</a>
  </article>

  <div class="pagination"><span class="arrow">&lsaquo;</span><span class="current">1</span><span>2</span><span>3</span><span>4</span><span class="arrow">&rsaquo;</span></div>

  <aside>
    <section class="widget" style="top:421px;height:155px">
      <h4 class="widget-title">ABOUT US</h4>
      <p>Pim Pim Nook is a local art home that shares the work of artists in our own town and helps you find pieces you love.</p>
      <a class="btn" href="#">READ MORE</a>
    </section>
    <section class="widget" style="top:598px;height:71px">
      <h4 class="widget-title">CONNECT US</h4>
      <div class="social"><span class="s1"></span><span class="s2"></span><span class="s3"></span><span class="s4"></span></div>
    </section>
    <section class="widget" style="top:692px;height:138px">
      <h4 class="widget-title">NEWSLETTER<br>SIGN UP</h4>
      <div class="email-field">Enter Email</div>
      <a class="btn" href="#">SIGN UP</a>
    </section>
  </aside>

  <footer class="site-footer">Copyright © 2015 Pim Pim Nook. All Rights Reserved. Privacy Policy</footer>
</body>
</html>
```